Fashion Women clothing Webpage design

I need help cleaning up my website page to put things in order change back round color. & make my page available to shop on. I do have a Wix add that just needs to get Edited the website name is www.thevelvetlantern.com I will send and invite through the wix app to give you permissions to be able to help assist and brainstorm any ideas you may have in addition must be wix savy because I am having trouble linking my webpage to public view and connecting through current domain you may also contact me through WhatsApp (731)586-2094 you may take a look to get a more Clear idea on what is needed for my website. I have more photos that are in my wix website folder that i would like to get organized in each specific item category please keep in my i would like for this to look like a online fashion boutique while being very creative and eye catchy.

Target Market(s)

I am looking to specifically target women who are into fashion & looking to plan or get ready for a special occasion to be able to come the velvet lantern and find what it is they are looking for.

Industry/Entity Type

Womens Clothing

Coding

Coded - Design and coding required

Number of Pages Required

4 page

Font styles to use
Sans Serif
Script

Colors

Designer to choose colors to be used in the design.

Requirements
Must have
• I would like that my project be able to have a items description available for the guest also that my project will be able to include sizes & colors I believe I have already done a little already but I can always go back in as need to be able to better assist you with my project if needed to do so for my projects completion.
Nice to have
• make this the greatest shop experiece for a women who is looking to shop for the best fashion. I would like to see that each item that has already been listed as new arrival be included on the main page so that the visitors are able to see my latest collection that is added. This will help them to see my new inventory especially for the consistent shoppers.
Should not have
• please keep certain colors that are not eye catchy to a minimum I am not to specific on colors because I am looking for a vibrant look to attract all guest as the name of my shop is :
• The Velvet Lantern.

```html
<!DOCTYPE html>
<html lang="en">
<head>
<meta charset="utf-8">
<title>The Velvet Lantern</title>
<link href="https://fonts.googleapis.com/css2?family=Lato:wght@400;700&display=swap" rel="stylesheet">
<style>
:root{
  --pink:#d9539a;
  --badge:#d46a9f;
  --ink:#333333;
  --muted:#555555;
  --line:#cfcfcf;
  --white:#ffffff;
}
*{margin:0;padding:0;box-sizing:border-box}
html,body{width:1200px;height:2296px;overflow:hidden;background:var(--white)}
body{position:relative;font-family:'Lato',sans-serif;color:var(--ink)}
.abs{position:absolute}
.site-header{position:absolute;left:0;top:0;width:1200px;height:95px}
.brand{position:absolute;left:146px;top:19px;width:200px;text-align:center;font-size:25px;line-height:30px;font-weight:400;color:#222;letter-spacing:0.5px}
.main-nav{position:absolute;left:424px;top:41px;display:flex;gap:22px;font-size:13.5px;color:#111}
.cart{position:absolute;left:998px;top:36px;width:40px;height:22px}
.hero-panel{left:0;top:95px;width:464px;height:528px;background:var(--pink)}
.hero-title{position:absolute;left:0;top:154px;width:464px;text-align:center;color:var(--white);font-size:36px;line-height:43px;font-weight:700}
.hero-button{position:absolute;left:182px;top:305px;width:156px;height:38px;border:1.5px solid var(--white);color:var(--white);font-size:13px;font-weight:700;display:flex;align-items:center;justify-content:center}
.photo{background-blend-mode:soft-light,normal}
.hero-photo{left:470px;top:95px;width:730px;height:528px;background:radial-gradient(ellipse 30% 60% at 62% 55%,#e9e2da 0%,rgba(233,226,218,0) 70%),linear-gradient(180deg,#cfccca 0%,#bdb8b4 60%,#a89a7c 100%)}
.category{top:631px;height:410px;display:flex;align-items:center;justify-content:center;color:var(--white);font-size:28px;font-weight:700;text-shadow:0 1px 3px rgba(0,0,0,.35)}
.cat-new{left:0;width:389px;background:radial-gradient(ellipse 35% 55% at 50% 55%,#c9a898 0%,rgba(201,168,152,0) 75%),linear-gradient(180deg,#2c241f,#4a3a30 60%,#8a7a70)}
.cat-top{left:396px;width:401px;background:radial-gradient(ellipse 30% 60% at 50% 55%,#c8b08a 0%,rgba(200,176,138,0) 75%),linear-gradient(180deg,#3a2e24,#6a5644 60%,#a08a72)}
.cat-fall{left:805px;width:395px;background:radial-gradient(ellipse 35% 55% at 50% 60%,#d9a6a6 0%,rgba(217,166,166,0) 75%),linear-gradient(180deg,#e4e4e4,#cfcfd2 60%,#bdbdc2)}
.section-title{position:absolute;left:0;width:1200px;text-align:center;font-size:30px;font-weight:700;color:var(--ink);line-height:34px}
.product{position:absolute;top:1155px;width:216px}
.product-photo{width:216px;height:295px}
.badge{position:absolute;left:0;top:0;width:112px;height:28px;background:var(--badge);color:var(--white);font-size:12px;display:flex;align-items:center;justify-content:center}
.product-name{margin-top:11px;text-align:center;font-size:17px;color:#333}
.product-rule{width:30px;height:2px;background:#333;margin:3px auto 0}
.product-price{margin-top:6px;text-align:center;font-size:13px;color:#333}
.feed{position:absolute;top:1688px;height:224px;width:240px}
.arrow{position:absolute;top:1790px;width:20px;height:34px}
.footer-col{position:absolute;top:1976px;width:220px;text-align:center}
.footer-col h3{font-size:21px;font-weight:700;color:#333;margin-bottom:9px}
.footer-col li{list-style:none;font-size:14px;color:#333;line-height:30.6px}
.newsletter-field{position:absolute;left:576px;top:2040px;width:205px;height:23px;border-bottom:1.5px solid #555;font-size:12px;color:var(--muted);display:flex;align-items:center;gap:8px;padding-left:6px}
.subscribe{position:absolute;left:574px;top:2079px;width:214px;height:44px;border:1.5px solid #777;font-size:15px;color:var(--muted);display:flex;align-items:center;justify-content:center}
.footer-rule{left:0;top:2233px;width:1200px;height:1px;background:var(--line)}
.copyright{left:0;top:2254px;width:1200px;text-align:center;font-size:13px;color:var(--muted)}
</style>
</head>
<body>
<header class="site-header">
  <div class="brand">THE VELVET LANTERN</div>
  <nav class="main-nav">
    <span>HOME</span><span>TOPS</span><span>DRESSES</span><span>JUMPSUITS</span><span>2 PIECE SETS</span><span>NEW ARRIVALS</span>
  </nav>
  <svg class="cart" viewBox="0 0 40 22" aria-label="Cart">
    <path d="M2 4h4l3 11h13l3-8H8" fill="none" stroke="#222" stroke-width="1.6"/>
    <circle cx="11" cy="19" r="1.6" fill="#222"/><circle cx="20" cy="19" r="1.6" fill="#222"/>
    <circle cx="33" cy="10" r="7" fill="#222"/>
    <text x="33" y="13.5" text-anchor="middle" font-size="9" fill="#fff" font-family="Lato,sans-serif">0</text>
  </svg>
</header>

<section class="abs hero-panel">
  <h1 class="hero-title">We Sell Top<br>Fashion Women<br>Clothing</h1>
  <div class="hero-button">Start Shopping</div>
</section>
<div class="abs hero-photo" role="img" aria-label="Model in a white tank top and gold metallic skirt"></div>

<div class="abs category cat-new" role="img" aria-label="Model in a blush bandage dress">New Arrivals</div>
<div class="abs category cat-top" role="img" aria-label="Model in a gold sequin jumpsuit">Top Collections</div>
<div class="abs category cat-fall" role="img" aria-label="Model in a pink strappy dress">Hot Fall Looks</div>

<h2 class="section-title" style="top:1097px">FEATURED</h2>

<article class="product" style="left:174px">
  <div class="product-photo" role="img" aria-label="Gold sequin mini dress" style="background:radial-gradient(ellipse 35% 50% at 50% 60%,#b89a70 0%,rgba(184,154,112,0) 75%),linear-gradient(180deg,#1d1a17,#2c2622)"></div>
  <span class="badge">NEW ARRIVAL</span>
  <div class="product-name">Product Title here</div><div class="product-rule"></div><div class="product-price">$25.00</div>
</article>
<article class="product" style="left:392px">
  <div class="product-photo" role="img" aria-label="Red bandage dress" style="background:radial-gradient(ellipse 30% 45% at 50% 65%,#b0141f 0%,rgba(176,20,31,0) 75%),linear-gradient(180deg,#1e1b1a,#2a2422)"></div>
  <span class="badge">NEW ARRIVAL</span>
  <div class="product-name">Product Title here</div><div class="product-rule"></div><div class="product-price">$25.00</div>
</article>
<article class="product" style="left:611px">
  <div class="product-photo" role="img" aria-label="Silver sequin off-shoulder dress" style="background:radial-gradient(ellipse 35% 45% at 50% 65%,#cfcccc 0%,rgba(207,204,204,0) 75%),linear-gradient(180deg,#2a2420,#4a3a30)"></div>
  <span class="badge">NEW ARRIVAL</span>
  <div class="product-name">Product Title here</div><div class="product-rule"></div><div class="product-price">$25.00</div>
</article>
<article class="product" style="left:828px">
  <div class="product-photo" role="img" aria-label="Nude bodycon dress" style="background:radial-gradient(ellipse 30% 50% at 50% 60%,#d8b090 0%,rgba(216,176,144,0) 75%),linear-gradient(180deg,#8a2e20,#7a2a1c)"></div>
  <span class="badge">NEW ARRIVAL</span>
  <div class="product-name">Product Title here</div><div class="product-rule"></div><div class="product-price">$25.00</div>
</article>

<h2 class="section-title" style="top:1587px">FOLLOW US ON<br>SNAPGRAM</h2>

<div class="feed" style="left:0;background:radial-gradient(ellipse 30% 55% at 55% 55%,#7c8090 0%,rgba(124,128,144,0) 75%),linear-gradient(180deg,#1c2330,#2c3444)" role="img" aria-label="Model in a glitter gown"></div>
<div class="feed" style="left:240px;background:radial-gradient(ellipse 30% 55% at 50% 55%,#b8322c 0%,rgba(184,50,44,0) 75%),linear-gradient(180deg,#5a4a3a,#7a6a58)" role="img" aria-label="Model in a red bandage dress"></div>
<div class="feed" style="left:480px;background:radial-gradient(ellipse 28% 60% at 50% 55%,#1e1a22 0%,rgba(30,26,34,0) 75%),linear-gradient(180deg,#5a2a3a,#c9a9b8)" role="img" aria-label="Model in a black mesh jumpsuit"></div>
<div class="feed" style="left:720px;background:radial-gradient(ellipse 30% 55% at 50% 60%,#111 0%,rgba(17,17,17,0) 75%),linear-gradient(180deg,#3a3038,#6a5a5c)" role="img" aria-label="Model in a black cut-out dress"></div>
<div class="feed" style="left:960px;background:radial-gradient(ellipse 45% 30% at 50% 60%,#6a5244 0%,rgba(106,82,68,0) 75%),linear-gradient(180deg,#111111,#2a2220)" role="img" aria-label="Model in a black dress on a sofa"></div>
<svg class="arrow" style="left:31px" viewBox="0 0 20 34" aria-label="Previous"><path d="M16 2L4 17l12 15" fill="none" stroke="#fff" stroke-width="2"/></svg>
<svg class="arrow" style="left:1144px" viewBox="0 0 20 34" aria-label="Next"><path d="M4 2l12 15L4 32" fill="none" stroke="#fff" stroke-width="2"/></svg>

<footer>
  <div class="footer-col" style="left:97px"><h3>Quick Links</h3><ul><li>Home</li><li>Shop</li><li>About</li><li>Forum</li><li>Contact</li></ul></div>
  <div class="footer-col" style="left:302px"><h3>Explore</h3><ul><li>FAQ</li><li>Shipping &amp; Returns</li><li>Store Policy</li><li>Payment Methods</li></ul></div>
  <div class="footer-col" style="left:528px;width:300px"><h3>Join Our Newsletter</h3></div>
  <div class="newsletter-field">
    <svg width="14" height="10" viewBox="0 0 14 10"><rect x="0.5" y="0.5" width="13" height="9" fill="none" stroke="#555"/><path d="M0.5 0.5l6.5 5 6.5-5" fill="none" stroke="#555"/></svg>
    Email address
  </div>
  <div class="subscribe">Subscribe Now</div>
  <div class="footer-col" style="left:831px"><h3>Follow</h3><ul><li>Friendbook</li><li>Chirper</li><li>Snapgram</li><li>Pinboard</li></ul></div>
  <div class="abs footer-rule"></div>
  <div class="abs copyright">© 2018 Company Name &nbsp;All rights reserved</div>
</footer>
</body>
</html>
```